holloway paving service

Needs to have phone number 0418259730 and email markholloway@brightmail.com.au.
ABN 62318470915
name mark holloway

For all your concreting solutions
Excavation
Exposed & colour concrete
House & shed slabs
Driveways
Landing & steps

Contact Information for Business Card

ph 0418259730
email markholloway@brightmail.com.au.
ABN 62318470915
name mark holloway

```html
<!DOCTYPE html>
<html lang="en">
<head>
<meta charset="utf-8">
<title>Holloway Paving Service – Business Card</title>
<link rel="stylesheet" href="https://fonts.googleapis.com/css2?family=Quicksand:wght@500;600;700&display=swap">
<style>
  :root {
    --canvas-bg: #e4e2df;
    --card-white: #f3f3f3;
    --card-white-edge: #e6e6e6;
    --brand-orange: #ea6a2a;
    --brand-orange-deep: #dc5f22;
    --brand-orange-soft: #f07a3a;
    --ink-grey: #5e5e5e;
    --rule-grey: #6b6b6b;
    --white: #ffffff;
  }
  * { box-sizing: border-box; margin: 0; padding: 0; }
  html, body {
    width: 1200px;
    height: 960px;
    overflow: hidden;
    background: var(--canvas-bg);
    font-family: "Quicksand", sans-serif;
  }
  .canvas { position: relative; width: 1200px; height: 960px; }

  .card { position: absolute; width: 600px; height: 342px; overflow: hidden; }

  /* Front */
  .card-front {
    left: 302px; top: 127px;
    background: linear-gradient(180deg, var(--card-white) 0%, var(--card-white-edge) 100%);
  }
  .brand-lockup { position: absolute; left: 296px; top: 36px; height: 74px; display: flex; align-items: center; }
  .brand-mark { width: 46px; height: 46px; background: var(--brand-orange); margin-right: 26px; }
  .brand-divider { width: 2px; height: 74px; background: var(--brand-orange); margin-right: 6px; }
  .brand-text { display: flex; flex-direction: column; align-items: center; width: 180px; }
  .brand-name {
    color: var(--brand-orange); font-weight: 700; font-size: 14px;
    line-height: 15px; letter-spacing: 0.2px; text-align: center;
  }
  .brand-rule { width: 100%; height: 2px; background: var(--rule-grey); margin: 4px 0 3px; }
  .brand-phone { color: var(--brand-orange); font-weight: 600; font-size: 12.5px; letter-spacing: 1px; }

  .holder { position: absolute; left: 33px; top: 250px; }
  .holder-name {
    color: var(--brand-orange); font-weight: 700; font-size: 23px;
    letter-spacing: 0.2px; line-height: 28px; text-transform: uppercase;
  }
  .holder-detail { color: var(--ink-grey); font-weight: 500; font-size: 14.5px; line-height: 21px; }

  /* Back */
  .card-back { left: 300px; top: 500px; width: 598px; }
  .back-texture {
    position: absolute; inset: 0;
    background: linear-gradient(90deg, var(--brand-orange-deep) 0%, var(--brand-orange-soft) 50%, var(--brand-orange-deep) 100%);
  }
  .back-brand { position: absolute; left: 128px; top: 128px; width: 110px; display: flex; flex-direction: column; align-items: center; }
  .back-mark { width: 14px; height: 14px; background: var(--white); margin-bottom: 8px; }
  .back-brand-name {
    color: var(--white); font-weight: 700; font-size: 14px; line-height: 17px;
    text-align: center; text-transform: uppercase;
  }
  .service-list { position: absolute; left: 252px; top: 125px; list-style: none; }
  .service-list li {
    color: var(--white); font-weight: 500; font-size: 14.5px; line-height: 18px;
    display: flex; align-items: center;
  }
  .service-list li::before {
    content: ""; width: 5px; height: 5px; background: var(--white);
    transform: rotate(45deg); margin-right: 8px;
  }
</style>
</head>
<body>
<main class="canvas">
  <section class="card card-front" aria-label="Business card front">
    <div class="brand-lockup">
      <div class="brand-mark"></div>
      <div class="brand-divider"></div>
      <div class="brand-text">
        <div class="brand-name">HOLLOWAY PAVING SERVICE</div>
        <div class="brand-rule"></div>
        <div class="brand-phone">0418259730</div>
      </div>
    </div>
    <div class="holder">
      <h1 class="holder-name">Mark Holloway</h1>
      <p class="holder-detail">markholloway@brightmail.com.au</p>
      <p class="holder-detail">ABN 62318470915</p>
    </div>
  </section>

  <section class="card card-back" aria-label="Business card back">
    <div class="back-texture" role="img" aria-label="Orange background with a faint repeating brand pattern"></div>
    <div class="back-brand">
      <div class="back-mark"></div>
      <div class="back-brand-name">Holloway<br>Paving<br>Service</div>
    </div>
    <ul class="service-list">
      <li>Excavation</li>
      <li>Exposed &amp; colour concrete</li>
      <li>House &amp; shed slabs</li>
      <li>Driveways</li>
      <li>Landing &amp; steps</li>
    </ul>
  </section>
</main>
</body>
</html>
```